Design NEW business card

We would like a business card using the colour deep red wine or dark navy blue textured background (patterned or not, open to suggestions) with a high gloss debossed rose gold/copper RM Roland Mercer Jewellery business name (Provided). I have included images for your review we would like to keep our currently logo and business name on the front but you can change the layout and positioning. For the back of the card we are open to all suggestions/variations.
Business
Use our current RM Roland Mercer Jewellery logo (Provided image)

```html
<!DOCTYPE html>
<html lang="en">
<head>
<meta charset="utf-8">
<title>Roland Mercer Jewellery – Business Card</title>
<link rel="stylesheet" href="https://fonts.googleapis.com/css2?family=Montserrat:wght@300;400;500&display=swap">
<style>
  :root {
    --backdrop: #a8a8a8;
    --card-white: #f7f7f6;
    --wine: #5a2129;
    --rose-gold: #c08a6a;
    --rose-gold-light: #d8a98a;
    --rose-gold-dark: #9e6e52;
    --ink-grey: #4a4a4a;
    --white: #ffffff;
  }
  * { margin: 0; padding: 0; box-sizing: border-box; }
  html, body {
    width: 1200px; height: 960px; overflow: hidden;
    background: var(--backdrop);
    font-family: "Montserrat", sans-serif;
  }
  .canvas { position: relative; width: 1200px; height: 960px; }

  .card {
    position: absolute;
    width: 604px; height: 342px;
    box-shadow: 0 3px 8px rgba(0,0,0,0.25);
    overflow: hidden;
  }

  /* Brand name block */
  .brand {
    position: absolute;
    display: flex; align-items: center; gap: 12px;
    color: var(--rose-gold);
    font-weight: 400;
  }
  .brand__dot {
    border-radius: 50%;
    background: var(--rose-gold);
    flex: none;
  }
  .brand__name { display: flex; flex-direction: column; }
  .brand__line { display: block; letter-spacing: 0.16em; line-height: 1.2; }
  .brand__line--sub { letter-spacing: 0.95em; margin-top: 4px; }

  /* Front */
  .card--front { left: 320px; top: 98px; background: var(--card-white); }
  .card--front .brand { left: 186px; top: 215px; font-size: 22px; }
  .card--front .brand__dot { width: 14px; height: 14px; }
  .card--front .brand__line--sub { font-size: 10px; }
  .website {
    position: absolute; left: 0; right: 0; top: 303px;
    text-align: center;
    font-size: 13px; letter-spacing: 0.42em;
    color: var(--ink-grey);
  }

  /* Back */
  .card--back { left: 320px; top: 493px; width: 600px; background: var(--wine); }
  .card__accent {
    position: absolute; top: 0; right: 0; width: 290px; height: 100%;
    background: linear-gradient(90deg, var(--rose-gold-dark), var(--rose-gold-light) 50%, var(--rose-gold-dark));
  }
  .card--back .brand { left: 66px; top: 128px; font-size: 17px; gap: 10px; }
  .card--back .brand__dot { width: 11px; height: 11px; }
  .card--back .brand__line--sub { font-size: 8px; margin-top: 3px; }
  .person { position: absolute; left: 33px; top: 190px; }
  .person__name { font-size: 19px; font-weight: 400; color: var(--rose-gold-light); letter-spacing: 0.02em; }
  .person__role { font-size: 12.5px; color: var(--white); margin-top: 4px; }
  .contact {
    position: absolute; right: 24px; top: 200px;
    color: var(--white); text-align: right;
    font-size: 14px; line-height: 19px;
  }
  .contact__address { margin-bottom: 8px; }
  .contact__row { display: flex; justify-content: flex-end; align-items: center; gap: 8px; }
  .contact__icon { width: 14px; height: 14px; flex: none; }
</style>
</head>
<body>
<main class="canvas">

  <section class="card card--front" aria-label="Card front">
    <div class="brand">
      <span class="brand__dot"></span>
      <span class="brand__name">
        <span class="brand__line">ROLAND MERCER</span>
        <span class="brand__line brand__line--sub">JEWELLERY</span>
      </span>
    </div>
    <p class="website">www.rmjewellery.com</p>
  </section>

  <section class="card card--back" aria-label="Card back">
    <div class="card__accent" role="img" aria-label="Rose gold and silver decorative sweep"></div>

    <div class="brand">
      <span class="brand__dot"></span>
      <span class="brand__name">
        <span class="brand__line">ROLAND MERCER</span>
        <span class="brand__line brand__line--sub">JEWELLERY</span>
      </span>
    </div>

    <div class="person">
      <p class="person__name">DANIEL HART</p>
      <p class="person__role">CEO/FOUNDER</p>
    </div>

    <div class="contact">
      <p class="contact__address">412 Larkspur Court<br>Fairbanks, Alaska 99701</p>
      <p class="contact__row">907 555 0142
        <svg class="contact__icon" viewBox="0 0 16 16"><path fill="currentColor" d="M3.6 1.5l2.3 2.6-1.3 1.8c.9 2 2.5 3.6 4.5 4.5l1.8-1.3 2.6 2.3-1.3 2.1C7 13.3 2.7 9 1.5 2.8z"/></svg>
      </p>
      <p class="contact__row">907 555 0187
        <svg class="contact__icon" viewBox="0 0 16 16"><rect x="4" y="1" width="8" height="14" rx="1.5" fill="none" stroke="currentColor" stroke-width="1.6"/><rect x="7" y="12" width="2" height="1.4" fill="currentColor"/></svg>
      </p>
      <p class="contact__row">907 555 0163
        <svg class="contact__icon" viewBox="0 0 16 16"><rect x="4" y="2" width="8" height="4" fill="currentColor"/><rect x="1" y="6" width="14" height="6" rx="1" fill="currentColor"/><rect x="4" y="10" width="8" height="4" fill="var(--rose-gold)" stroke="currentColor"/></svg>
      </p>
      <p class="contact__row">hello@rmjewellery.com
        <svg class="contact__icon" viewBox="0 0 16 16"><rect x="1" y="3.5" width="14" height="9.5" fill="currentColor"/><path d="M1 3.5l7 5.5 7-5.5" fill="none" stroke="var(--rose-gold-dark)" stroke-width="1.2"/></svg>
      </p>
    </div>
  </section>

</main>
</body>
</html>
```